Corvane Holdings , new business card design

investment firm with corporate clients . need double sided business card , vertical and horizontal options ,logo must be clear. prefer pantone colors only and sharp design. website also www.corvane.ae

Khalid Bin Tarrafi
Managing Director
Tel. +971 4 387 2940
Mobile +971 50 518 2403
khalid@corvane.ae
Q-Span Plaza, officw 18-B07, Warqa Gardens, Dubai

Contact Information for Business Card

Khalid Bin Tarrafi
Managing Director

Font styles to use
Serif

Colors

Designer to choose colors to be used in the design.

```html
<!DOCTYPE html>
<html lang="en">
<head>
<meta charset="utf-8">
<title>Corvane Holdings — Business Card</title>
<link rel="stylesheet" href="https://fonts.googleapis.com/css2?family=Roboto:wght@300;400&family=Roboto+Condensed:wght@700&display=swap">
<style>
  :root {
    --backdrop: #dedede;
    --card-white: #f4f4f4;
    --brand-blue: #436d92;
    --name-blue: #3f6590;
    --ink: #1c1c1c;
    --body-grey: #454545;
    --white: #ffffff;
  }
  * { margin: 0; padding: 0; box-sizing: border-box; }
  html, body { width: 1200px; height: 960px; overflow: hidden; }
  body {
    background: var(--backdrop);
    position: relative;
    font-family: "Roboto", Arial, sans-serif;
  }
  .card {
    position: absolute;
    width: 600px;
    height: 342px;
  }
  .card--front { left: 314px; top: 113px; background: var(--card-white); }
  .card--back  { left: 311px; top: 472px; background: var(--brand-blue); }

  .wordmark {
    position: absolute;
    font-family: "Roboto", Arial, sans-serif;
    font-weight: 300;
    text-transform: uppercase;
    line-height: 1;
  }
  .wordmark__main { display: block; font-size: 36px; letter-spacing: 13px; }
  .wordmark__sub  { display: block; font-size: 12px; letter-spacing: 11.5px; margin-top: 6px; padding-left: 2px; }

  .card--front .wordmark { left: 47px; top: 52px; color: var(--ink); }
  .card--back .wordmark {
    left: 0; right: 0; top: 138px; text-align: center; color: var(--white);
  }
  .card--back .wordmark__main { font-size: 44px; letter-spacing: 17px; padding-left: 17px; }
  .card--back .wordmark__sub  { font-size: 14px; letter-spacing: 14px; padding-left: 14px; margin-top: 9px; }

  .holder {
    position: absolute;
    right: 42px;
    top: 57px;
    text-align: right;
  }
  .holder__name {
    font-family: "Roboto Condensed", "Arial Narrow", sans-serif;
    font-weight: 700;
    font-size: 20px;
    color: var(--name-blue);
    line-height: 24px;
  }
  .holder__title {
    font-size: 15px;
    color: var(--ink);
    line-height: 20px;
  }

  .contact {
    position: absolute;
    left: 47px;
    list-style: none;
    font-size: 14.5px;
    color: var(--body-grey);
  }
  .contact li {
    position: relative;
    padding-left: 24px;
    line-height: 19px;
  }
  .contact .icon {
    position: absolute;
    left: 0;
    top: 3px;
    width: 14px;
    height: 14px;
    fill: var(--brand-blue);
  }
  .contact--address { top: 161px; }
  .contact--address li { line-height: 18px; }
  .contact--lines { top: 226px; }

  .web-address {
    position: absolute;
    left: 0; right: 0;
    top: 288px;
    text-align: center;
    color: var(--white);
    font-size: 14px;
    letter-spacing: 13.5px;
    padding-left: 13.5px;
  }
</style>
</head>
<body>

<section class="card card--front" aria-label="Business card front">
  <div class="wordmark">
    <span class="wordmark__main">Corvane</span>
    <span class="wordmark__sub">Holdings</span>
  </div>

  <div class="holder">
    <p class="holder__name">Khalid Bin Tarrafi</p>
    <p class="holder__title">Managing Director</p>
  </div>

  <ul class="contact contact--address">
    <li>
      <svg class="icon" viewBox="0 0 14 14" aria-hidden="true"><path d="M7 0a5 5 0 0 0-5 5c0 3.6 5 9 5 9s5-5.4 5-9a5 5 0 0 0-5-5zm0 7a2 2 0 1 1 0-4 2 2 0 0 1 0 4z"/></svg>
      Q-Span Plaza<br>officw 18-B07, Warqa Gardens<br>Dubai
    </li>
  </ul>

  <ul class="contact contact--lines">
    <li>
      <svg class="icon" viewBox="0 0 14 14" aria-hidden="true"><path d="M3 .5l2.3 2.8-1.2 1.7c.9 1.9 2.3 3.3 4.2 4.2l1.7-1.2 2.8 2.3-1.3 2.6C6 12.4 1.6 8 .4 1.8z"/></svg>
      +971 4 387 2940
    </li>
    <li>
      <svg class="icon" viewBox="0 0 14 14" aria-hidden="true"><path d="M3.5 0h7a1 1 0 0 1 1 1v12a1 1 0 0 1-1 1h-7a1 1 0 0 1-1-1V1a1 1 0 0 1 1-1zm.6 1.6v9.4h5.8V1.6zM7 11.6a.7.7 0 1 0 0 1.4.7.7 0 0 0 0-1.4z"/></svg>
      +971 50 518 2403
    </li>
    <li>
      <svg class="icon" viewBox="0 0 14 14" aria-hidden="true"><path d="M1 3h12v1L7 8 1 4zm0 2.3l6 4 6-4V11H1z"/></svg>
      khalid@corvane.ae
    </li>
    <li>
      <svg class="icon" viewBox="0 0 14 14" aria-hidden="true"><path d="M7 1a6 6 0 1 0 0 12A6 6 0 0 0 7 1zm-.8 10.7A4.8 4.8 0 0 1 2.3 6l2.9 2.9v.6c0 .6.5 1 1 1zm3.9-1.4c-.2-.5-.6-.8-1.1-.8h-.6V8.2c0-.3-.2-.6-.6-.6H4.6V6.4h1.2c.3 0 .6-.2.6-.6V4.6h1.2c.7 0 1.2-.5 1.2-1.2v-.2a4.8 4.8 0 0 1 1.3 7.1z"/></svg>
      www.corvane.ae
    </li>
  </ul>
</section>

<section class="card card--back" aria-label="Business card back">
  <div class="wordmark">
    <span class="wordmark__main">Corvane</span>
    <span class="wordmark__sub">Holdings</span>
  </div>
  <p class="web-address">www.corvane.ae</p>
</section>

</body>
</html>
```